Preisliste für Kosmetikinstitut
Zielgruppe
Ich benötige für mein Kosmetikinstitut eine Preisliste für die moderne Frau, aber auch Männer. Das Design sollte mein Logo enthalten. Farben des Designkonzepts einbauen.
A4 quer zum Falten, wie ein Heft, 1. Seite Preisliste mit logo, im Innenteil dann Anwendungen
Aufgabenstellung
Minimalistisch, ästhetisch, modern, edel
Kontaktdaten auf der Rückseite
LB Hautatelier
Lotte Brenner
Lindenhang 17
83671 Waakirchen
EMail: lotte@lb-hautatelier.de
Whatsapp: 0176 284 9017

```html
<!DOCTYPE html>
<html lang="de">
<head>
<meta charset="utf-8">
<title>Preisliste – LB Hautatelier</title>
<link href="https://fonts.googleapis.com/css2?family=Questrial&family=Mrs+Saint+Delafield&display=swap" rel="stylesheet">
<style>
  :root{
    --backdrop:#3f5853;
    --paper:#f5f5f3;
    --band:#e4e3e0;
    --accent:#3e5a55;
    --text:#5e605f;
    --muted:#8a8c8b;
    --photo-light:#e9e9e8;
    --photo-dark:#bdbebd;
  }
  *{box-sizing:border-box;margin:0;padding:0}
  html,body{width:1200px;height:900px;overflow:hidden}
  body{background:var(--backdrop);font-family:"Questrial",sans-serif;color:var(--text);position:relative}

  .spread{position:absolute;left:290px;width:620px;height:436px;display:flex;background:var(--paper);box-shadow:0 8px 24px rgba(0,0,0,.25)}
  .spread--outside{top:10px}
  .spread--inside{top:454px}
  .page{position:relative;width:310px;height:100%;overflow:hidden}
  .page + .page{border-left:1px solid #e2e2e0}

  /* outside */
  .brand{position:absolute;bottom:26px;font-size:10px;letter-spacing:1px;color:var(--accent);display:flex;align-items:center;gap:5px;text-transform:uppercase}
  .brand__dot{width:6px;height:6px;border-radius:50%;background:var(--accent)}
  .page--back .brand{left:26px}
  .page--cover .brand{right:26px}
  .contact{position:absolute;left:26px;bottom:50px;font-style:normal;font-size:8px;line-height:1.6;color:var(--text)}
  .contact__name{color:var(--accent)}
  .cover__texture{position:absolute;left:0;top:0;width:66px;height:100%;background:linear-gradient(160deg,var(--photo-light),var(--photo-dark) 45%,var(--photo-light) 70%,var(--photo-dark))}
  .cover__title{position:absolute;right:28px;top:44px;font-family:"Mrs Saint Delafield",cursive;font-size:64px;color:var(--accent);font-weight:400;line-height:1}

  /* inside */
  .section-bar{background:var(--band);height:22px;display:flex;align-items:center;padding:0 12px;font-size:10px;color:var(--accent);margin-bottom:9px}
  .page--left .section-bar{width:190px}
  .page--right .section-bar{width:200px;margin-left:auto;justify-content:flex-end}
  .page__body{padding:0 20px}
  .page--left,.page--right{padding-top:22px}
  .treatment{margin-bottom:6px}
  .treatment__head{display:flex;justify-content:space-between;align-items:flex-end;font-size:7.4px;color:var(--accent)}
  .treatment__price{white-space:nowrap;padding-left:8px}
  .treatment__desc{font-size:4.6px;line-height:1.35;margin-top:2px;color:var(--text)}
  .steps{list-style:none;font-size:4.6px;line-height:1.4;margin-top:2px}
  .rates{margin-top:2px;font-size:4.8px;color:var(--muted)}
  .rates div{display:flex;justify-content:flex-end;gap:8px}
  .rates span:last-child{width:26px;text-align:right;color:var(--text)}
  .extras{list-style:none;font-size:6px;line-height:1.6}
  .extras li{display:flex;justify-content:space-between}
</style>
</head>
<body>

<section class="spread spread--outside" aria-label="Außenseite">
  <div class="page page--back">
    <address class="contact">
      <div class="contact__name">Lotte Brenner</div>
      <div>Lindenhang 17</div>
      <div>83671 Waakirchen</div>
      <div>E-Mail: lotte@lb-hautatelier.de</div>
      <div>WhatsApp: 0176 284 9017</div>
    </address>
    <div class="brand"><span class="brand__dot"></span>LB Hautatelier</div>
  </div>
  <div class="page page--cover">
    <div class="cover__texture" role="img" aria-label="Foto einer transparenten Gel-Textur mit Wassertropfen"></div>
    <h1 class="cover__title">Preisliste</h1>
    <div class="brand"><span class="brand__dot"></span>LB Hautatelier</div>
  </div>
</section>

<section class="spread spread--inside" aria-label="Innenseite">
  <div class="page page--left">
    <div class="section-bar">Gesichtsbehandlungen</div>
    <div class="page__body">
      <div class="treatment">
        <div class="treatment__head"><span>Express Facial Treatment</span><span class="treatment__price">35-45 Min. | € 59</span></div>
        <p class="treatment__desc">Für alle, die wenig Zeit haben und trotzdem ihre Haut auffrischen und revitalisieren wollen. Reinigung, Enzympeeling, Serum, Maske, Abschlusspflege</p>
      </div>
      <div class="treatment">
        <div class="treatment__head"><span>Classic Facial Treatment –<br>Klassische Gesichtsbehandlung</span><span class="treatment__price">45-60 Min. | € 89</span></div>
        <p class="treatment__desc">Reinigung, Enzympeeling, Vapozon, Ausreinigung, Augenbrauenkorrektur, Ampulle, Massage, Maske, individuelle Abschlusspflege</p>
      </div>
      <div class="treatment">
        <div class="treatment__head"><span>Clear Skin Treatment</span><span class="treatment__price">50-60 Min. | € 89</span></div>
        <p class="treatment__desc">Die Haut wird ausgeglichen, Unreinheiten werden sanft reduziert, der Teint erhält Balance und kann sich beruhigen. Fältchen werden sichtbar gemildert.</p>
      </div>
      <div class="treatment">
        <div class="treatment__head"><span>Capillarine Treatment</span><span class="treatment__price">50-60 Min. | € 89</span></div>
        <p class="treatment__desc">Hautrötungen und Couperose werden gelindert, die Gefäßwände gestärkt und das Hautbild ausgeglichen. Hochkonzentrierte Wirkstoffe sorgen für Frische, Vitalität und Glätte.</p>
      </div>
      <div class="treatment">
        <div class="treatment__head"><span>Sensation Soft Treatment<br>(für die empfindliche, gereizte Haut)</span><span class="treatment__price">ca. 50 Min. | € 79</span></div>
        <p class="treatment__desc">Entzündliche Prozesse können gemildert werden, gereizte Haut wird beruhigt. Die Widerstandskraft der Haut wird gestärkt und sie erhält Balance.</p>
      </div>
      <div class="treatment">
        <div class="treatment__head"><span>Vitamin Soft Boost</span><span class="treatment__price">ca. 50 Min. | € 79</span></div>
        <p class="treatment__desc">Vitamine sorgen für Power und Frische in und auf der Haut. Die Fältchentiefe wird sichtbar verringert.</p>
      </div>
      <div class="treatment">
        <div class="treatment__head"><span>Anti-Age Advanced</span><span class="treatment__price">50-70 Min. (je nach Peeling) | € 99</span></div>
        <p class="treatment__desc">Die Haut wird intensiv entfaltet, vitalisiert und gestrafft. Feine Linien und Fältchen werden reduziert.</p>
      </div>
      <div class="treatment">
        <div class="treatment__head"><span>Chemisches Peeling (Oktober – April)</span><span class="treatment__price">€ XX</span></div>
        <p class="treatment__desc">Professionelle Peelings können viele Problemstellungen lindern, verbessern oder gar beheben. Dazu gehören die Zellerneuerung, Glättung der Hautstruktur und Reduzierung von Pigmentflecken.</p>
      </div>
    </div>
  </div>

  <div class="page page--right">
    <div class="section-bar">Apparative Behandlungen</div>
    <div class="page__body">
      <div class="treatment">
        <div class="treatment__head"><span>AQUAveil – Radiant Glow Treatment</span><span class="treatment__price">60 Min. | € 140</span></div>
        <p class="treatment__desc">In 6 Schritten zu einer Haut mit einmaligem Glow-Effekt</p>
        <ol class="steps">
          <li>1. die Haut wird tiefengereinigt</li>
          <li>2. die obersten Hornschüppchen werden sanft gelöst</li>
          <li>3. die Haut wird in der Tiefe gereinigt und entstopft</li>
          <li>4. ein Wirkstoffkonzentrat wird eingeschleust</li>
          <li>5. pflegende Maske beruhigt und versorgt die Haut</li>
          <li>6. zum Schluss werden die Essenzen eingearbeitet</li>
        </ol>
      </div>
      <div class="treatment">
        <div class="treatment__head"><span>Mikrodermabrasion</span></div>
        <p class="treatment__desc">Bei der Mikrodermabrasion handelt es sich um ein mechanisches Hautpeeling, dabei werden mit Hilfe feiner Kristalle die Hornzellen abgetragen. Die Haut wirkt frischer, Poren verfeinert und Pigmentflecken gemildert.</p>
        <div class="rates">
          <div><span>Gesicht</span><span>€ 89</span></div>
          <div><span>Gesicht, Hals, Dekolleté</span><span>€ 89</span></div>
        </div>
      </div>
      <div class="treatment">
        <div class="treatment__head"><span>Microneedling</span></div>
        <p class="treatment__desc">Die Behandlung eignet sich besonders für Menschen, die ihre Hautstruktur verbessern und Falten, Aknenarben, Pigmentverschiebungen sowie große Poren behandeln wollen. Feine Nadeln regen die Kollagenbildung an.</p>
        <div class="rates">
          <div><span>Gesicht</span><span>€ 110</span></div>
          <div><span>Gesicht, Hals</span><span>€ 130</span></div>
          <div><span>Gesicht, Hals, Dekolleté</span><span>€ 150</span></div>
        </div>
      </div>
    </div>
    <div class="section-bar">Zusatzleistungen</div>
    <div class="page__body">
      <ul class="extras">
        <li><span>Augenbrauen zupfen</span><span>€ 8</span></li>
        <li><span>Augenbrauen färben</span><span>€ 12</span></li>
        <li><span>Wimpern färben</span><span>€ 15</span></li>
        <li><span>Enthaarung störender Gesichtsbehaarung mittels Wax</span><span>€ 10-30</span></li>
      </ul>
    </div>
  </div>
</section>

</body>
</html>
```